Flyer für Vermietung von Autos und Mietkauf
Zielgruppe
Vermietung von Autos und Mietkauf Lösungen
Aufgabenstellung
Wichtig ist dass die Farben unserer CI benutzt werden. Am Besten an www.velaro-mobil.de orientieren. Der Flyer soll eine kurze Vorstellung des Mietkauf Modells sein.
Es geht um folgendes:
Kunden haben die Möglichkeit über uns Autos zu 'finanzieren' (Mietkauf). Der Kunde kann sich ein beliebiges Fahrzeug im Netz aussuchen (muss MwSt haben) und über uns mietkaufen. Er muss 35% des Fahrzeugpreises anbezahlen und der Vertrag läuft 2 Jahre. Danach kann er das Fahrzeug zum Restwert rauskaufen. Das ganze ohne Bonitätsprüfung und KRENTA. Es soll ein informatives PDF sein, welches ich potentiellen Kunden per Mail oder WhatsApp schicke. Es geht primär um Luxusfahrzeuge wie Corvanto ZXRs oder auch Castellunis. Das Design sollte also daran angelehnt sein.

```html
<!DOCTYPE html>
<html lang="de">
<head>
<meta charset="utf-8">
<title>Velaro Mobil – Mietkauf Flyer</title>
<link href="https://fonts.googleapis.com/css2?family=Lato:wght@400;700;900&display=swap" rel="stylesheet">
<style>
  :root {
    --bg: #d9d9d9;
    --ink: #1e1c1d;
    --gold: #c9b47a;
    --white: #ffffff;
    --grey: #bdbdbd;
    --grey-soft: #e6e6e6;
    --silver-dark: #2b2b2b;
    --silver-light: #d7d7d7;
  }
  * { box-sizing: border-box; margin: 0; padding: 0; }
  html, body { width: 1200px; height: 1200px; overflow: hidden; }
  body { background: var(--bg); font-family: "Lato", sans-serif; }

  .flyer {
    position: absolute; left: 160px; top: 20px;
    width: 880px; height: 1160px;
    background: var(--ink); overflow: hidden;
  }
  .flyer__backdrop { position: absolute; inset: 0; }

  .brand-strip {
    position: absolute; left: 0; top: 40px; width: 430px; height: 58px;
    background: linear-gradient(90deg, var(--silver-dark) 0%, #6a6a6a 25%, var(--silver-light) 60%, #8a8a8a 85%, var(--ink) 100%);
    display: flex; align-items: center; padding-left: 60px; gap: 14px;
  }
  .brand-strip__mark { width: 22px; height: 22px; background: var(--ink); }
  .brand-strip__name { color: var(--ink); font-size: 18px; font-weight: 400; letter-spacing: 0.5px; line-height: 1; }
  .brand-strip__name small { display: block; font-size: 9px; font-weight: 400; text-align: right; margin-top: 3px; letter-spacing: 0.3px; }

  .headline {
    position: absolute; left: 100px; top: 122px;
    color: var(--white); font-size: 44px; line-height: 1.15; font-weight: 700;
  }
  .headline .light { font-weight: 400; }
  .headline .line2 { display: block; padding-left: 14px; font-weight: 400; }

  .benefit {
    position: absolute; right: 0; height: 72px;
    background: var(--gold);
    color: var(--ink); font-size: 19px; line-height: 1.15; font-weight: 400;
    padding: 14px 0 0 90px;
  }
  .benefit strong { font-weight: 700; }
  .benefit--1 { top: 250px; left: 40px; }
  .benefit--2 { top: 342px; left: 60px; }
  .benefit--3 { top: 434px; left: 80px; }
  .benefit__streaks { position: absolute; right: 0; top: 0; width: 180px; height: 72px; }

  .hero-car {
    position: absolute; left: 210px; top: 520px; width: 640px; height: 150px;
    border-radius: 20px;
    background: linear-gradient(180deg, #d8d8d8 0%, #bcbcbc 55%, #8e8e8e 100%);
  }

  .partner-row {
    position: absolute; left: 150px; right: 90px; top: 690px;
    display: flex; justify-content: space-between; align-items: center;
  }
  .partner-badge { width: 30px; height: 30px; border-radius: 50%; background: var(--grey); }

  .side-car {
    position: absolute; left: 0; top: 780px; width: 340px; height: 300px;
    background: linear-gradient(135deg, #6b6b6b 0%, #1c1c1c 55%, #3a3a3a 100%);
    border-radius: 0 40px 40px 0;
  }

  .intro-text {
    position: absolute; left: 370px; top: 790px; width: 470px;
    color: var(--ink); font-size: 13.5px; line-height: 1.38;
  }

  .signature {
    position: absolute; left: 420px; top: 990px; width: 140px; height: 70px;
    background: var(--grey-soft); border-radius: 6px;
  }

  .phone-box {
    position: absolute; left: 600px; top: 1005px; width: 250px; height: 48px;
    background: var(--white); border: 2px solid var(--ink);
    box-shadow: 0 6px 14px rgba(0,0,0,0.25);
    display: flex; align-items: center; justify-content: center;
    font-size: 16px; font-weight: 700; color: var(--ink);
  }
</style>
</head>
<body>
  <main class="flyer">
    <svg class="flyer__backdrop" viewBox="0 0 880 1160" preserveAspectRatio="none" aria-hidden="true">
      <polygon points="0,640 880,580 880,1160 0,1160" fill="#ffffff"/>
      <polygon points="340,930 880,900 880,1000 560,1160 420,1160" fill="#ececec"/>
      <polygon points="600,1160 880,1010 880,1160" fill="#e1e1e1"/>
      <polygon points="0,1080 340,1080 250,1160 0,1160" fill="#f0f0f0"/>
    </svg>

    <div class="brand-strip">
      <span class="brand-strip__mark"></span>
      <span class="brand-strip__name">VELARO MOBIL<small>LUXURY CAR RENTAL</small></span>
    </div>

    <h1 class="headline"><span class="light">Ihr</span> High-End-Auto ist näher<span class="line2">als Sie denken.</span></h1>

    <div class="benefit benefit--1">Niedrige Anzahlung<br>von 35 %
      <svg class="benefit__streaks" viewBox="0 0 180 72" aria-hidden="true"><g stroke="#fff" stroke-width="1.5" opacity="0.8"><line x1="30" y1="6" x2="180" y2="6"/><line x1="60" y1="14" x2="180" y2="14"/><line x1="20" y1="22" x2="180" y2="22"/><line x1="80" y1="30" x2="180" y2="30"/><line x1="50" y1="38" x2="180" y2="38"/><line x1="100" y1="46" x2="180" y2="46"/></g></svg>
    </div>
    <div class="benefit benefit--2">Schneller<br>2-Jahres-Plan
      <svg class="benefit__streaks" viewBox="0 0 180 72" aria-hidden="true"><g stroke="#fff" stroke-width="1.5" opacity="0.8"><line x1="40" y1="6" x2="180" y2="6"/><line x1="70" y1="14" x2="180" y2="14"/><line x1="25" y1="22" x2="180" y2="22"/><line x1="90" y1="30" x2="180" y2="30"/><line x1="55" y1="38" x2="180" y2="38"/><line x1="110" y1="46" x2="180" y2="46"/></g></svg>
    </div>
    <div class="benefit benefit--3"><strong>KEINE</strong> Bonitätsprüfung.<br><strong>KEINE</strong> KRENTA
      <svg class="benefit__streaks" viewBox="0 0 180 72" aria-hidden="true"><g stroke="#fff" stroke-width="1.5" opacity="0.8"><line x1="35" y1="6" x2="180" y2="6"/><line x1="65" y1="14" x2="180" y2="14"/><line x1="20" y1="22" x2="180" y2="22"/><line x1="85" y1="30" x2="180" y2="30"/></g></svg>
    </div>

    <div class="hero-car" role="img" aria-label="Foto eines silbernen Sportwagens in Seitenansicht"></div>

    <div class="partner-row" aria-label="Partnermarken">
      <span class="partner-badge"></span><span class="partner-badge"></span><span class="partner-badge"></span><span class="partner-badge"></span>
      <span class="partner-badge"></span><span class="partner-badge"></span><span class="partner-badge"></span><span class="partner-badge"></span>
    </div>

    <div class="side-car" role="img" aria-label="Foto eines schwarzen Sportwagens in Frontansicht"></div>

    <p class="intro-text">Mit Velaro Mobil wird Ihr Traumwagen Wirklichkeit, und das einfacher, als Sie es sich vorstellen. Profitieren Sie von einer niedrigen Anzahlung ab nur 35% und einem transparenten 2-Jahres-Plan, der Ihnen finanzielle Flexibilität bietet – ganz ohne Bonitätsprüfung oder KRENTA-Eintrag. Das Beste daran: Sie wählen Ihr Wunschfahrzeug selbst aus, und wir kümmern uns um den Kauf für Sie. Am Ende der Laufzeit haben Sie die Option, das Fahrzeug zum Restwert zu übernehmen. Eine wichtige Voraussetzung ist lediglich, dass das Fahrzeug die Mehrwertsteuer (MwSt.) ausweisbar ist, um Ihnen den bestmöglichen Service bieten zu können.</p>

    <div class="signature" role="img" aria-label="Handschriftliche Unterschrift von Jonas"></div>

    <div class="phone-box">+49 (0)30 555 014 288</div>
  </main>
</body>
</html>
```